Automotive eCommerce Business looking for a business card design

Looking for a clean and simple business card design. Our company name is "Brindle Auto" and we are a company specializing in the ecommerce sales of automotive parts, specifically for pick up trucks and large SUVs. Our company colours are red, black, and white.

Feel free to use the logo provided or create a new logo that you seem fit. Looking forward to your creative ideas!

Industry/Entity Type

Automotive

Contact Information for Business Card

We were thinking of a possibly two-sided design featuring just the logo and company name on one side, and personal information on the other side. Single sided designs will be considered as well.

Font styles to use
Serif
Sans Serif
Decorative

Colors
ec1f27
ffffff
000000

Requirements
Must have
• Space for employee's name, title, phone number and email address, along with the company address and website somewhere.

```html
<!DOCTYPE html>
<html lang="en">
<head>
<meta charset="utf-8">
<title>Brindle Auto – Business Card</title>
<link rel="stylesheet" href="https://fonts.googleapis.com/css2?family=Roboto:wght@400;500&display=swap">
<style>
  :root {
    --backdrop: #d9d4cf;
    --card-red: #7c1c25;
    --card-red-light: #962d38;
    --card-red-deep: #6a141c;
    --tab-white: #ece8e6;
    --text-light: #f3e4e4;
    --brand-red: #6e1820;
  }
  html, body {
    margin: 0;
    padding: 0;
    width: 1200px;
    height: 969px;
    overflow: hidden;
    background: var(--backdrop);
  }
  .canvas {
    position: relative;
    width: 1200px;
    height: 969px;
  }
  .business-card {
    position: absolute;
    left: 165px;
    top: 237px;
    width: 870px;
    height: 495px;
    border-radius: 22px;
    overflow: hidden;
    box-shadow: 0 18px 40px rgba(0,0,0,0.18);
    font-family: "Roboto", Arial, sans-serif;
    color: var(--text-light);
  }
  .card-shapes {
    position: absolute;
    inset: 0;
  }
  .holder-name {
    position: absolute;
    left: 47px;
    top: 38px;
    font-size: 28px;
    font-weight: 500;
    letter-spacing: 0.5px;
    margin: 0;
  }
  .holder-title {
    position: absolute;
    left: 47px;
    top: 76px;
    font-size: 20px;
    font-weight: 400;
    letter-spacing: 0.5px;
    margin: 0;
  }
  .company-address {
    position: absolute;
    left: 47px;
    top: 247px;
    font-size: 20px;
    line-height: 26px;
    font-style: normal;
  }
  .contact-list {
    position: absolute;
    left: 47px;
    top: 315px;
    margin: 0;
    padding: 0;
    list-style: none;
    font-size: 19px;
  }
  .contact-list li {
    display: flex;
    align-items: center;
    height: 28px;
  }
  .contact-list svg {
    width: 18px;
    height: 18px;
    margin-right: 16px;
    fill: var(--text-light);
  }
  .brand-block {
    position: absolute;
    left: 425px;
    top: 0;
    width: 445px;
    height: 300px;
    display: flex;
    flex-direction: column;
    align-items: center;
  }
  .brand-square {
    margin-top: 45px;
    width: 120px;
    height: 120px;
    background: var(--brand-red);
    border-radius: 4px;
  }
  .brand-name {
    margin-top: 40px;
    font-size: 32px;
    font-weight: 500;
    color: var(--brand-red);
    letter-spacing: 0.5px;
  }
</style>
</head>
<body>
<div class="canvas">
  <div class="business-card">
    <svg class="card-shapes" width="870" height="495" viewBox="0 0 870 495" aria-hidden="true">
      <defs>
        <radialGradient id="cardRedGlow" cx="0.3" cy="0.35" r="0.8">
          <stop offset="0" stop-color="var(--card-red-light)"/>
          <stop offset="0.6" stop-color="var(--card-red)"/>
          <stop offset="1" stop-color="var(--card-red-deep)"/>
        </radialGradient>
      </defs>
      <rect class="card-base" width="870" height="495" fill="url(#cardRedGlow)"/>
      <path class="brand-tab" d="M425 0 H870 V255 L650 352 Q640 356 630 352 L455 262 Q425 248 425 215 Z" fill="var(--tab-white)"/>
    </svg>

    <h1 class="holder-name">OWEN HALE</h1>
    <p class="holder-title">CEO/FOUNDER</p>

    <address class="company-address">4120 Larkspur Road<br>Fairbanks, Alaska 34690</address>

    <ul class="contact-list">
      <li><svg viewBox="0 0 24 24"><path d="M6.6 10.8a15.1 15.1 0 0 0 6.6 6.6l2.2-2.2a1 1 0 0 1 1-.25 11.4 11.4 0 0 0 3.6.57 1 1 0 0 1 1 1V20a1 1 0 0 1-1 1A17 17 0 0 1 3 4a1 1 0 0 1 1-1h3.5a1 1 0 0 1 1 1c0 1.25.2 2.45.57 3.57a1 1 0 0 1-.25 1Z"/></svg>555 214 0187</li>
      <li><svg viewBox="0 0 24 24"><path d="M7 1h10a2 2 0 0 1 2 2v18a2 2 0 0 1-2 2H7a2 2 0 0 1-2-2V3a2 2 0 0 1 2-2Zm0 3v14h10V4Zm5 15.2a1.2 1.2 0 1 0 0 2.4 1.2 1.2 0 0 0 0-2.4Z"/></svg>555 309 7742</li>
      <li><svg viewBox="0 0 24 24"><path d="M6 2h12v5H6Zm-3 6h18a2 2 0 0 1 2 2v7h-4v5H5v-5H1v-7a2 2 0 0 1 2-2Zm4 8v4h10v-4Z"/></svg>555 468 2016</li>
      <li><svg viewBox="0 0 24 24"><path d="M2 5h20v14H2Zm2 2v.5l8 5 8-5V7Zm0 2.8V17h16V9.8l-8 5Z"/></svg>owen@brindleauto.com</li>
      <li><svg viewBox="0 0 24 24"><path d="M12 2a10 10 0 1 0 0 20 10 10 0 0 0 0-20Zm-1 17.9A8 8 0 0 1 4.1 11H7l2 2v2l2 2Zm6.9-2.6A2 2 0 0 0 16 16h-1v-3a1 1 0 0 0-1-1H8v-2h2a1 1 0 0 0 1-1V7h2a2 2 0 0 0 2-2v-.4a8 8 0 0 1 2.9 12.7Z"/></svg>www.brindleauto.com</li>
    </ul>

    <div class="brand-block">
      <div class="brand-square"></div>
      <div class="brand-name">Brindle Auto Ltd.</div>
    </div>
  </div>
</div>
</body>
</html>
```